Investment company needing business card

We are wanting a business card which looks sharp and easy on the eye. We are thinking of having a business card with the logo embossed on it, to really make it stand out. We will only have a small amount of information of the business card, person's name, position, email address and phone number

Contact Information for Business Card

Danielle Frost
Executive Assistant
+64 21 473 5162
danielf@harwickpartners.co.nz

Requirements
Must have
• Embossed logo
Should not have
• Not to be busy

```html
<!DOCTYPE html>
<html lang="en">
<head>
<meta charset="utf-8">
<title>Harwick Partners – Business Cards</title>
<link rel="stylesheet" href="https://fonts.googleapis.com/css2?family=Open+Sans:wght@400;600;700&display=swap">
<style>
  :root {
    --green: #22b573;
    --grey: #5f6062;
    --text: #4d4d4f;
    --paper: #ffffff;
    --backdrop: #e6e3e1;
  }
  * { margin: 0; padding: 0; box-sizing: border-box; }
  html, body { width: 1200px; height: 997px; overflow: hidden; }
  body {
    background: var(--backdrop);
    font-family: "Open Sans", Arial, sans-serif;
    position: relative;
  }
  .card {
    position: absolute;
    width: 520px;
    height: 300px;
    background: var(--paper);
    overflow: hidden;
    box-shadow: 0 6px 18px rgba(0,0,0,.12);
  }
  .card svg.shapes { position: absolute; inset: 0; }

  /* Front card */
  .card--front { left: 70px; top: 150px; }
  .brand {
    position: absolute;
    right: 34px;
    top: 34px;
    display: flex;
    align-items: center;
    gap: 10px;
  }
  .brand__mark { width: 30px; height: 30px; background: var(--grey); }
  .brand__name {
    color: var(--green);
    font-weight: 700;
    font-size: 22px;
    letter-spacing: 1px;
  }
  .person { position: absolute; left: 34px; top: 90px; }
  .person__name { color: var(--green); font-weight: 700; font-size: 15px; text-transform: uppercase; }
  .person__role { color: var(--text); font-size: 12.5px; margin-top: 2px; }
  .contact { position: absolute; left: 34px; top: 152px; list-style: none; }
  .contact li {
    display: flex; align-items: center; gap: 7px;
    color: var(--text); font-size: 12.5px; line-height: 18px;
  }
  .contact svg { width: 10px; height: 10px; fill: var(--green); }

  /* Back card */
  .card--back { left: 610px; top: 500px; }
  .media-name {
    position: absolute;
    right: 26px; top: 40px;
    color: #fff;
    display: flex; align-items: center; gap: 10px;
  }
  .media-name__mark { width: 24px; height: 24px; border-radius: 50%; background: #fff; }
  .media-name__text { font-weight: 700; font-size: 20px; letter-spacing: 1px; line-height: 24px; text-align: right; }
  .media-name__text span { display: block; }
  .placeholder { position: absolute; left: 30px; top: 100px; }
  .placeholder__name { color: var(--green); font-weight: 700; font-size: 20px; }
  .placeholder__title { color: var(--green); font-size: 13px; }
  .rows { position: absolute; left: 30px; top: 158px; list-style: none; }
  .rows li { display: flex; align-items: center; margin-bottom: 4px; }
  .rows__icon {
    width: 22px; height: 22px; background: var(--green);
    display: flex; align-items: center; justify-content: center;
  }
  .rows__icon svg { width: 11px; height: 11px; fill: #fff; }
  .rows__text {
    border: 1px solid var(--green); border-left: none;
    height: 22px; width: 210px; padding-left: 10px;
    color: var(--green); font-size: 12px; line-height: 20px;
  }
  .address { position: absolute; left: 30px; top: 240px; color: var(--green); font-size: 12px; line-height: 16px; }
</style>
</head>
<body>

<section class="card card--front" aria-label="Business card front">
  <svg class="shapes" viewBox="0 0 520 300" aria-hidden="true">
    <path d="M0 284 C200 270 380 220 520 110 L520 300 L0 300 Z" fill="var(--green)"/>
    <path d="M0 276 C200 262 380 210 520 98 L520 106 C380 216 200 268 0 281 Z" fill="var(--grey)"/>
  </svg>
  <div class="brand">
    <span class="brand__mark"></span>
    <span class="brand__name">HARWICK PARTNERS</span>
  </div>
  <div class="person">
    <p class="person__name">Danielle Frost</p>
    <p class="person__role">Executive Assistant</p>
  </div>
  <ul class="contact">
    <li><svg viewBox="0 0 10 10"><path d="M2 0 L4 2 L3 3.5 C4 5 5 6 6.5 7 L8 6 L10 8 L8.5 10 C4 9 1 6 0 1.5 Z"/></svg>+64 21 473 5162</li>
    <li><svg viewBox="0 0 10 10"><path d="M0 2 H10 V8 H0 Z M0 2 L5 5.5 L10 2" stroke="#fff" stroke-width=".8"/></svg>danielf@harwickpartners.co.nz</li>
    <li><svg viewBox="0 0 10 10"><circle cx="5" cy="5" r="5"/></svg>www.harwickpartners.co.nz</li>
  </ul>
</section>

<section class="card card--back" aria-label="Business card alternate side">
  <svg class="shapes" viewBox="0 0 520 300" aria-hidden="true">
    <path d="M150 0 H520 V240 Z" fill="var(--green)"/>
  </svg>
  <div class="media-name">
    <span class="media-name__mark"></span>
    <p class="media-name__text"><span>NORTHBAY MEDIA</span><span>COMPANY</span></p>
  </div>
  <div class="placeholder">
    <p class="placeholder__name">Your Name</p>
    <p class="placeholder__title">Title</p>
  </div>
  <ul class="rows">
    <li><span class="rows__icon"><svg viewBox="0 0 10 10"><path d="M2 0 L4 2 L3 3.5 C4 5 5 6 6.5 7 L8 6 L10 8 L8.5 10 C4 9 1 6 0 1.5 Z"/></svg></span><span class="rows__text">123-456-7890</span></li>
    <li><span class="rows__icon"><svg viewBox="0 0 10 10"><path d="M0 2 H10 V8 H0 Z"/></svg></span><span class="rows__text">info@northbaymedia.com</span></li>
    <li><span class="rows__icon"><svg viewBox="0 0 10 10"><circle cx="5" cy="5" r="5"/></svg></span><span class="rows__text">www.northbaymedia.com</span></li>
  </ul>
  <p class="address">Street Name, City Name,<br>Zip Code - 00000</p>
</section>

</body>
</html>
```